Letterhead, stationery and email signature for construction business

I need the letterhead, stationery and email signature designs for a construction business. I want them to have a corporate feel to them.

I've attached the logo for reference.

```html
<!DOCTYPE html>
<html lang="en">
<head>
<meta charset="utf-8">
<title>Harlow Build Letterhead</title>
<link href="https://fonts.googleapis.com/css2?family=Open+Sans:wght@400;700&display=swap" rel="stylesheet">
<style>
  :root {
    --backdrop: #e4e4e4;
    --paper: #ffffff;
    --brand-blue: #2e56a8;
    --accent-blue: #1a73c8;
    --ink: #2b2b33;
    --wash: #f3f3f8;
  }
  html, body {
    margin: 0;
    width: 1200px;
    height: 1141px;
    overflow: hidden;
    background: var(--backdrop);
  }
  .letterhead {
    position: absolute;
    left: 210px;
    top: 20px;
    width: 779px;
    height: 1101px;
    background: var(--paper);
    box-shadow: 0 4px 18px rgba(0,0,0,0.18);
    font-family: "Open Sans", sans-serif;
    color: var(--ink);
    overflow: hidden;
  }
  .brand {
    position: absolute;
    left: 39px;
    top: 55px;
    display: flex;
    align-items: center;
    gap: 14px;
  }
  .brand-square {
    width: 80px;
    height: 80px;
    background: var(--brand-blue);
  }
  .brand-name {
    display: flex;
    flex-direction: column;
    font-weight: 700;
    color: var(--brand-blue);
    line-height: 1;
  }
  .brand-name-main {
    font-size: 50px;
    letter-spacing: 0.5px;
  }
  .brand-name-sub {
    font-size: 24px;
    letter-spacing: 17px;
    margin-top: 4px;
  }
  .divider {
    position: absolute;
    left: 510px;
    top: 45px;
    width: 2px;
    height: 111px;
    background: var(--accent-blue);
  }
  .contact {
    position: absolute;
    left: 539px;
    top: 38px;
    font-size: 18px;
    line-height: 22.5px;
  }
  .contact p { margin: 0; }
  .contact .address { margin-bottom: 7px; }
  .contact-line {
    display: flex;
    align-items: center;
    gap: 6px;
  }
  .contact-line svg {
    width: 13px;
    height: 13px;
    flex: none;
    fill: var(--accent-blue);
  }
  .watermark {
    position: absolute;
    left: 108px;
    top: 199px;
    width: 562px;
    height: 702px;
    background: radial-gradient(ellipse at center, var(--wash) 0%, rgba(243,243,248,0.5) 40%, rgba(255,255,255,0) 72%);
  }
</style>
</head>
<body>
  <main class="letterhead">
    <header>
      <div class="brand">
        <div class="brand-square"></div>
        <span class="brand-name">
          <span class="brand-name-main">HARLOW</span>
          <span class="brand-name-sub">BUILD</span>
        </span>
      </div>
      <div class="divider"></div>
      <div class="contact">
        <p class="address">Your address, City<br>State, Zip 1234</p>
        <p class="contact-line">
          <svg viewBox="0 0 16 16" aria-hidden="true"><path d="M1 6c2-3 12-3 14 0l-1 2-3-1V5.5C9.5 5 6.5 5 5 5.5V7L2 8z"/><path d="M4 9h8l2 5H2z"/></svg>
          123 456 789
        </p>
        <p class="contact-line">
          <svg viewBox="0 0 16 16" aria-hidden="true"><path d="M1 4h14v1L8 9 1 5z"/><path d="M1 6.5l7 4 7-4V12H1z"/></svg>
          info@yourgmail.com
        </p>
        <p class="contact-line">
          <svg viewBox="0 0 16 16" aria-hidden="true"><circle cx="8" cy="8" r="7"/><path d="M4 5c2 0 3 1 2 3s1 3 0 5M10 3c-1 2 1 3 3 3" stroke="#fff" stroke-width="1.3" fill="none"/></svg>
          www.yourwebsite.com
        </p>
      </div>
    </header>
    <div class="watermark" role="img" aria-label="Faint brand watermark wash"></div>
  </main>
</body>
</html>
```